VANTOL GROUP

This is a company that provides executive protection. Our motto is "New Era in Protection"... I don't want this to look like other security websites. I want it to be clean and sharp and represent a new era. We are based in the bay area so maybe a picture of San Francisco in the background?
I want it to be able to funnel down a couple different categories.
1. About Us
2. Services (Executive Protection, Covert Protection, Residential Protection & Intelligence)
3. Blue Maple (Training & Consulting)
4. Contact Us
I want it to be very clean and modern. I don't want there to be any pictures of bodyguards with ear pieces like every other website.
Target Market(s)
Ultra High Net Worth Individuals
Coding
Coded - Design and coding required
Number of Pages Required
1 page
Requirements
Must have
- Colors of my Symbol
Nice to have
- City in the background, San Francisco, New York or the Pinecrest Lodge in Montana.
Should not have
- Should not look like an KVM website or have photos of bodyguards. I want this to be a clean and simple website with my logo

```html
<!DOCTYPE html>
<html lang="en">
<head>
<meta charset="utf-8">
<title>VANTOL GROUP — New Era in Protection</title>
<link rel="stylesheet" href="https://fonts.googleapis.com/css2?family=Lato:wght@400;700;900&family=Orbitron:wght@900&display=swap">
<style>
:root{
  --red:#7c0d16;
  --red-deep:#5e0910;
  --red-bright:#9a1420;
  --ink:#111111;
  --text-grey:#7a7a7a;
  --white:#ffffff;
  --footer-dark:#1b1b1b;
}
*{margin:0;padding:0;box-sizing:border-box}
html,body{width:1200px;height:2914px;overflow:hidden}
body{position:relative;background:var(--white);font-family:"Lato",sans-serif;color:var(--ink)}
.abs{position:absolute}
svg{display:block}

/* top bar */
.top-bar{left:0;top:0;width:1200px;height:34px}
.top-call{left:720px;top:0;height:34px;line-height:34px;color:var(--white);font-size:13px;font-weight:700;display:flex;align-items:center;gap:8px}
.top-social{left:944px;top:9px;display:flex;gap:12px}
.social-dot{width:16px;height:16px;border-radius:50%;background:var(--white)}

/* header */
.site-header{left:0;top:34px;width:1200px;height:90px;background:var(--white)}
.main-nav{top:34px;height:90px;display:flex;align-items:center;font-size:16px;font-weight:700;color:var(--ink)}
.nav-link{position:absolute;top:70px;font-size:16px;font-weight:700;color:var(--ink);letter-spacing:-0.2px}
.nav-active-line{left:597px;top:119px;width:85px;height:4px;background:var(--red)}
.nav-active-tip{left:633px;top:113px;width:0;height:0;border-left:6px solid transparent;border-right:6px solid transparent;border-bottom:6px solid var(--red)}
.logo-badge{left:139px;top:-28px;width:226px;height:226px;border-radius:50%;background:var(--white);z-index:3}
.logo-square{left:233px;top:42px;width:38px;height:38px;background:var(--red);z-index:4}
.logo-name{left:139px;top:104px;width:226px;text-align:center;font-weight:900;font-size:23px;color:var(--ink);letter-spacing:1px;z-index:4}

/* hero */
.hero{left:0;top:124px;width:1200px;height:686px}
.hero-title{left:0;top:318px;width:1200px;text-align:center;font-family:"Orbitron",sans-serif;font-weight:900;font-size:66px;line-height:80px;color:var(--white);letter-spacing:2px;text-shadow:0 3px 6px rgba(0,0,0,.45)}
.btn{position:absolute;display:flex;align-items:center;justify-content:center;background:var(--red);color:var(--white);font-weight:700;border-radius:40px;letter-spacing:-0.2px}
.btn-hero{left:493px;top:525px;width:215px;height:69px;font-size:20px}
.slider-dots{left:548px;top:695px;display:flex;gap:10px}
.dot{width:12px;height:12px;border-radius:50%;background:var(--white)}
.dot.is-active{background:var(--red)}

/* about */
.about-bg{left:0;top:814px;width:1200px;height:540px;background:linear-gradient(180deg,#ffffff 0%,#f4f2f2 45%,#e6e3e3 70%,#ffffff 100%)}
.about-visual{left:145px;top:891px;width:382px;height:407px}
.section-title{position:absolute;font-family:"Orbitron",sans-serif;font-weight:900;font-size:40px;color:var(--ink);letter-spacing:1px}
.about-title{left:602px;top:880px}
.body-copy{position:absolute;font-size:14.5px;line-height:25.6px;color:var(--text-grey)}
.about-copy{left:602px;top:956px;width:448px}
.btn-read{width:180px;height:58px;font-size:17px}
.about-btn{left:602px;top:1193px}

/* services */
.service-panel{top:1353px;width:392px;height:475px}
.service-panel.panel-exec{left:0}
.service-panel.panel-covert{left:401px;width:397px}
.service-panel.panel-res{left:808px}
.service-shape{position:absolute;left:0;top:0}
.service-icon{position:absolute;top:38px;left:50%;transform:translateX(-50%)}
.service-name{position:absolute;left:0;top:186px;width:100%;text-align:center;color:var(--white);font-weight:900;font-size:25px;line-height:34px;letter-spacing:-0.3px}
.service-text{position:absolute;left:0;width:100%;text-align:center;color:var(--white);font-size:19px;line-height:28px}
.service-chevron{position:absolute;left:50%;transform:translateX(-50%);top:456px}

/* blue maple */
.maple-bg{left:0;top:1866px;width:1200px;height:560px;background:linear-gradient(180deg,#ffffff 0%,#f3f1f1 45%,#e4e1e1 75%,#ffffff 100%)}
.maple-title{left:145px;top:1946px}
.maple-copy{left:145px;top:2021px;width:448px}
.maple-btn{left:145px;top:2257px}
.maple-visual{left:625px;top:1920px;width:440px;height:440px}

/* footer */
.site-footer{left:0;top:2430px;width:1200px;height:484px}
.footer-brand{left:0;top:2612px;width:1200px;display:flex;justify-content:center;align-items:center;gap:22px}
.footer-square{width:64px;height:64px;background:#b9b9b9}
.footer-name{font-weight:900;font-size:46px;color:#b9b9b9;letter-spacing:2px}
.footer-nav{left:0;top:2720px;width:1200px;text-align:center;font-size:26px;font-weight:700;color:var(--white);letter-spacing:-0.3px}
.footer-nav .sep{margin:0 26px}
.footer-legal{left:0;top:2786px;width:1200px;text-align:center;font-size:14px;color:var(--white)}
.footer-social{left:528px;top:2848px;display:flex;gap:20px}
.footer-social .social-dot{width:22px;height:22px}
</style>
</head>
<body>

<!-- top bar -->
<svg class="abs top-bar" width="1200" height="34" viewBox="0 0 1200 34">
  <polygon points="0,0 1200,0 1200,0 1166,34 34,34" fill="#6b0a12"/>
</svg>
<div class="abs top-call">
  <svg width="12" height="12" viewBox="0 0 24 24"><path d="M6.6 10.8a15.1 15.1 0 0 0 6.6 6.6l2.2-2.2c.3-.3.7-.4 1-.2 1.1.4 2.3.6 3.6.6.6 0 1 .4 1 1V20c0 .6-.4 1-1 1A17 17 0 0 1 3 4c0-.6.4-1 1-1h3.5c.6 0 1 .4 1 1 0 1.3.2 2.5.6 3.6.1.3 0 .7-.2 1z" fill="#fff"/></svg>
  <span>CALL US : 1 800 555 0142</span>
</div>
<div class="abs top-social" aria-label="Social links">
  <span class="social-dot"></span><span class="social-dot"></span><span class="social-dot"></span><span class="social-dot"></span>
</div>

<!-- header -->
<header class="abs site-header"></header>
<nav>
  <a class="nav-link" style="left:602px">ABOUT US</a>
  <a class="nav-link" style="left:724px">SERVICES</a>
  <a class="nav-link" style="left:840px">BLUE MAPLE</a>
  <a class="nav-link" style="left:955px">CONTACT US</a>
</nav>
<div class="abs nav-active-tip"></div>
<div class="abs nav-active-line"></div>

<!-- hero -->
<svg class="abs hero" width="1200" height="686" viewBox="0 0 1200 686" role="img" aria-label="Dusk aerial view of the San Francisco skyline and Bay Bridge with city lights">
  <defs>
    <linearGradient id="heroSky" x1="0" y1="0" x2="0" y2="1">
      <stop offset="0" stop-color="#4a5670"/>
      <stop offset="0.35" stop-color="#2f3d5a"/>
      <stop offset="0.62" stop-color="#3b3440"/>
      <stop offset="0.78" stop-color="#6a3a2a"/>
      <stop offset="1" stop-color="#1d2536"/>
    </linearGradient>
  </defs>
  <polygon points="0,526 1200,526 600,686" fill="var(--red)"/>
  <polygon points="0,0 1200,0 1200,532 600,656 0,532" fill="url(#heroSky)"/>
</svg>
<div class="abs logo-badge"></div>
<div class="abs logo-square"></div>
<div class="abs logo-name">VANTOL GROUP</div>
<h1 class="abs hero-title">NEW ERA IN<br>PROTECTION</h1>
<a class="btn btn-hero">GET STARTED</a>
<div class="abs slider-dots">
  <span class="dot"></span><span class="dot"></span><span class="dot is-active"></span><span class="dot"></span><span class="dot"></span>
</div>

<!-- about -->
<div class="abs about-bg" role="img" aria-label="Faded misty mountain landscape"></div>
<svg class="abs about-visual" width="382" height="407" viewBox="0 0 382 407" role="img" aria-label="Red-toned photo of a professional in a suit">
  <defs>
    <linearGradient id="aboutPhoto" x1="0" y1="0" x2="1" y2="1">
      <stop offset="0" stop-color="#c8404a"/>
      <stop offset="0.55" stop-color="#9a1a24"/>
      <stop offset="1" stop-color="#5e0910"/>
    </linearGradient>
  </defs>
  <rect width="382" height="407" fill="url(#aboutPhoto)"/>
</svg>
<h2 class="section-title about-title">ABOUT US</h2>
<p class="body-copy about-copy">Lorem ipsum dolor sit amet, consectetur adipiscing elid do eiusmod tempor incididunt ut labore et dolore magna aliqis ipsum suspendisse ultrices gravida. Risus commodo viverra maecenas accumsan lacus vel facilisiorem ipsum dolor sit amet, consectetur adipiscing ed do eiusmod tempor incididunt ut labore et dolore magna aliqis ipsum suspendisse ultrices gravus commodo viverra maecenas accumsan lacus vel facirem ipsum dolor sonsectdipiscing elit, sed do eiusmod tempor incididunt ut labore et dolore magna aliqis ipsum suspendisse</p>
<a class="btn btn-read about-btn">READ MORE</a>

<!-- services -->
<section class="abs service-panel panel-exec">
  <svg class="service-shape" width="392" height="475" viewBox="0 0 392 475" role="img" aria-label="Dark red photo of an executive in a car">
    <defs><linearGradient id="execBg" x1="0" y1="0" x2="0" y2="1"><stop offset="0" stop-color="#8e1520"/><stop offset="1" stop-color="#5a0810"/></linearGradient></defs>
    <polygon points="0,0 392,0 392,383 228,468 196,436 164,468 0,383" fill="url(#execBg)"/>
  </svg>
  <svg class="service-icon" width="112" height="112" viewBox="0 0 112 112" fill="none" stroke="#fff" stroke-width="3">
    <circle cx="40" cy="24" r="14"/>
    <path d="M8 108V78c0-12 10-20 22-20h20c8 0 14 4 17 10"/>
    <path d="M34 58l6 14 6-14M40 72v34"/>
    <rect x="56" y="72" width="52" height="36" rx="3"/>
    <path d="M72 72v-8h20v8M56 88h52"/>
  </svg>
  <h3 class="service-name">EXECUTIVE PROTECTION</h3>
  <p class="service-text" style="top:240px">Lorem ipsum dolor sitconsectetur<br>adipiscing elised do eiusmod<br>tempor incididunt ut labore<br>et dolore magna aliqua.</p>
  <svg class="service-chevron" width="18" height="22" viewBox="0 0 18 22" fill="none" stroke="var(--red)" stroke-width="3"><path d="M2 2l7 7 7-7M2 12l7 7 7-7"/></svg>
</section>

<section class="abs service-panel panel-covert">
  <svg class="service-shape" width="397" height="475" viewBox="0 0 397 475" role="img" aria-label="Dark photo of a hooded figure">
    <polygon points="0,0 397,0 397,383 231,468 198,436 165,468 0,383" fill="#0b0b0b"/>
  </svg>
  <svg class="service-icon" width="100" height="112" viewBox="0 0 100 112" fill="none" stroke="#fff" stroke-width="3">
    <path d="M50 4l42 14v34c0 28-18 48-42 56C26 100 8 80 8 52V18z"/>
    <path d="M50 14l32 11v27c0 22-14 38-32 45-18-7-32-23-32-45V25z"/>
    <rect x="34" y="50" width="32" height="26" rx="3"/>
    <path d="M40 50v-8a10 10 0 0 1 20 0v8"/>
    <circle cx="50" cy="61" r="3"/><path d="M50 64v6"/>
  </svg>
  <h3 class="service-name">COVERT PROTECTION</h3>
  <p class="service-text" style="top:240px">Lorem ipsum dolor sitconsectetur<br>adipiscing elised do eiusmod<br>tempor incididunt ut labore<br>et dolore magna aliqua.</p>
  <svg class="service-chevron" width="18" height="22" viewBox="0 0 18 22" fill="none" stroke="var(--red)" stroke-width="3"><path d="M2 2l7 7 7-7M2 12l7 7 7-7"/></svg>
</section>

<section class="abs service-panel panel-res">
  <svg class="service-shape" width="392" height="475" viewBox="0 0 392 475" role="img" aria-label="Red-toned photo of hands holding a small house">
    <defs><linearGradient id="resBg" x1="0" y1="0" x2="0" y2="1"><stop offset="0" stop-color="#9a1822"/><stop offset="1" stop-color="#620a12"/></linearGradient></defs>
    <polygon points="0,0 392,0 392,383 228,468 196,436 164,468 0,383" fill="url(#resBg)"/>
  </svg>
  <svg class="service-icon" width="116" height="112" viewBox="0 0 116 112" fill="none" stroke="#fff" stroke-width="3">
    <path d="M4 50L58 6l54 44"/>
    <path d="M16 40v64h84V40"/>
    <path d="M4 104h108"/>
    <path d="M58 36l18 6v12c0 12-8 20-18 24-10-4-18-12-18-24V42z"/>
    <path d="M50 56l6 6 11-12"/>
  </svg>
  <h3 class="service-name">RESIDENTIAL PROTECTION<br>&amp; INTELLIGENCE</h3>
  <p class="service-text" style="top:270px">Lorem ipsum dolor sitconsectetur<br>adipiscing elised do eiusmod<br>tempor incididunt ut labore</p>
  <svg class="service-chevron" width="18" height="22" viewBox="0 0 18 22" fill="none" stroke="var(--red)" stroke-width="3"><path d="M2 2l7 7 7-7M2 12l7 7 7-7"/></svg>
</section>

<!-- blue maple -->
<div class="abs maple-bg" role="img" aria-label="Faded misty mountain landscape"></div>
<h2 class="section-title maple-title">BLUE MAPLE</h2>
<p class="body-copy maple-copy">Lorem ipsum dolor sit amet, consectetur adipiscing elid do eiusmod tempor incididunt ut labore et dolore magna aliqis ipsum suspendisse ultrices gravida. Risus commodo viverra maecenas accumsan lacus vel facilisiorem ipsum dolor sit amet, consectetur adipiscing ed do eiusmod tempor incididunt ut labore et dolore magna aliqis ipsum suspendisse ultrices gravus commodo viverra maecenas accumsan lacus vel facirem ipsum dolor sonsectdipiscing elit, sed do eiusmod tempor incididunt ut labore et dolore magna aliqis ipsum suspendisse</p>
<a class="btn btn-read maple-btn">READ MORE</a>
<svg class="abs maple-visual" width="440" height="440" viewBox="0 0 440 440" role="img" aria-label="Photo of a consultant presenting at a whiteboard to a meeting">
  <defs>
    <linearGradient id="maplePhoto" x1="0" y1="0" x2="1" y2="1">
      <stop offset="0" stop-color="#e9e9e7"/>
      <stop offset="0.5" stop-color="#c9c6c2"/>
      <stop offset="1" stop-color="#8a8580"/>
    </linearGradient>
  </defs>
  <circle cx="226" cy="216" r="214" fill="var(--red)"/>
  <circle cx="218" cy="218" r="210" fill="#ffffff"/>
  <circle cx="218" cy="218" r="199" fill="url(#maplePhoto)"/>
</svg>

<!-- footer -->
<svg class="abs site-footer" width="1200" height="484" viewBox="0 0 1200 484" role="img" aria-label="Dark misty mountain silhouette">
  <defs><linearGradient id="footBg" x1="0" y1="0" x2="0" y2="1"><stop offset="0" stop-color="#2a2a2a"/><stop offset="1" stop-color="#0e0e0e"/></linearGradient></defs>
  <polygon points="600,4 1200,154 1200,484 0,484 0,154" fill="var(--red)"/>
  <polygon points="600,36 1200,162 1200,484 0,484 0,162" fill="url(#footBg)"/>
</svg>
<div class="abs footer-brand"><span class="footer-square"></span><span class="footer-name">VANTOL GROUP</span></div>
<nav class="abs footer-nav">ABOUT US<span class="sep">/</span>SERVICES<span class="sep">/</span>BLUE MAPLE<span class="sep">/</span>CONTACT US</nav>
<p class="abs footer-legal">© 2021 Vantol Group. All rights reserved &nbsp;|&nbsp; Privacy &nbsp;|&nbsp; Terms of Use</p>
<div class="abs footer-social" aria-label="Social links">
  <span class="social-dot"></span><span class="social-dot"></span><span class="social-dot"></span><span class="social-dot"></span>
</div>

</body>
</html>
```